Lumavento business card

We need a modern business card - With our 4 colors - See web: www.lumavento.dk

I have attached logo and som old business Cards we have - Lets Make the new ones shine...:-) -

Industry/Entity Type

Business

Requirements
Must have
• the logo with lumavento only,

```html
<!DOCTYPE html>
<html lang="da">
<head>
<meta charset="utf-8">
<title>Lumavento – visitkort</title>
<link rel="stylesheet" href="https://fonts.googleapis.com/css2?family=Source+Sans+3:wght@300;400;600&display=swap">
<style>
  :root {
    --bg: #ecebea;
    --orange: #f38a22;
    --lime: #a9cb38;
    --rose: #ea3a78;
    --magenta: #e8148a;
    --purple: #6b2a7d;
    --ink: #ffffff;
  }
  * { box-sizing: border-box; margin: 0; padding: 0; }
  html, body { width: 1200px; height: 900px; overflow: hidden; background: var(--bg); }
  body { position: relative; font-family: "Source Sans 3", sans-serif; color: var(--ink); }

  .card {
    position: absolute;
    overflow: hidden;
    background: linear-gradient(to bottom,
      var(--orange) 0%, var(--orange) 6%,
      var(--lime) 28%, var(--lime) 34%,
      var(--rose) 52%, var(--magenta) 62%,
      var(--magenta) 82%, var(--purple) 100%);
    box-shadow: 0 6px 18px rgba(0,0,0,0.18);
  }
  .card--front { left: 238px; top: 62px; width: 555px; height: 342px; }
  .card--back  { left: 457px; top: 518px; width: 560px; height: 343px; }

  /* front */
  .brand-name {
    position: absolute; left: 0; width: 100%; text-align: center;
    font-weight: 300; letter-spacing: 3px;
  }
  .card--front .brand-name { top: 96px; font-size: 26px; }
  .brand-rule { position: absolute; height: 2px; background: var(--ink); }
  .card--front .brand-rule { left: 177px; width: 200px; top: 152px; }
  .tagline {
    position: absolute; top: 165px; left: 0; width: 100%;
    text-align: center; font-size: 11px; font-weight: 300;
  }
  .person { position: absolute; right: 291px; top: 209px; text-align: right; }
  .person__name { font-size: 19px; font-weight: 600; line-height: 1.2; }
  .person__role { font-size: 14px; font-weight: 400; margin-top: 2px; }

  .contact { position: absolute; left: 287px; top: 199px; list-style: none; }
  .contact li { display: flex; align-items: center; height: 23.5px; font-size: 14px; }
  .contact svg { width: 11px; height: 11px; margin-right: 14px; fill: var(--ink); flex: none; }

  .address {
    position: absolute; left: 0; right: 0; top: 297px;
    display: flex; align-items: center; gap: 10px; font-size: 14px; white-space: nowrap;
  }
  .address::before, .address::after {
    content: ""; flex: 1; height: 1px; background: rgba(255,255,255,0.75);
  }

  /* back */
  .card--back .brand-name { top: 118px; font-size: 44px; letter-spacing: 5px; }
  .back-name {
    position: absolute; top: 229px; left: 0; width: 100%;
    text-align: center; font-size: 17px; letter-spacing: 2px;
  }
  .card--back .brand-rule { left: 136px; width: 288px; top: 256px; height: 3px; }
  .back-role {
    position: absolute; top: 262px; left: 0; width: 100%;
    text-align: center; font-size: 16px; letter-spacing: 2px; font-weight: 600;
  }
</style>
</head>
<body>
  <section class="card card--front">
    <div class="brand-name">lumavento</div>
    <div class="brand-rule"></div>
    <p class="tagline">Medier til unge</p>

    <div class="person">
      <p class="person__name">Aksel Vindberg</p>
      <p class="person__role">Salgsdirektør</p>
    </div>

    <ul class="contact">
      <li>
        <svg viewBox="0 0 24 24" aria-hidden="true"><path d="M6.6 10.8a15.1 15.1 0 0 0 6.6 6.6l2.2-2.2c.3-.3.7-.4 1-.2 1.1.4 2.3.6 3.6.6.6 0 1 .4 1 1V20c0 .6-.4 1-1 1A17 17 0 0 1 3 4c0-.6.4-1 1-1h3.5c.6 0 1 .4 1 1 0 1.3.2 2.5.6 3.6.1.3 0 .7-.2 1z"/></svg>
        +45 40 12 34 56
      </li>
      <li>
        <svg viewBox="0 0 24 24" aria-hidden="true"><path d="M2 5h20v14H2zm2 2v.5l8 5 8-5V7l-8 5z"/></svg>
        av@lumavento.dk
      </li>
      <li>
        <svg viewBox="0 0 24 24" aria-hidden="true"><path d="M12 2a10 10 0 1 0 0 20 10 10 0 0 0 0-20zm-1 17.9A8 8 0 0 1 4.1 10L9 15v1a2 2 0 0 0 2 2zm6.9-2.5A2 2 0 0 0 16 16h-1v-3a1 1 0 0 0-1-1H8v-2h2a1 1 0 0 0 1-1V7h2a2 2 0 0 0 2-2v-.4a8 8 0 0 1 2.9 12.8z"/></svg>
        www.lumavento.dk
      </li>
    </ul>

    <p class="address">Lindholms Allé 12 - 2000 Frederiksberg -Tlf. 38 40 17 22</p>
  </section>

  <section class="card card--back">
    <div class="brand-name">lumavento</div>
    <p class="back-name">Aksel Vindberg</p>
    <div class="brand-rule"></div>
    <p class="back-role">Salgsdirektør</p>
  </section>
</body>
</html>
```